Navoro & Omvar Automotive Repair Shop. Need a new website design.

We specialize in Navoro & Omvar auto repair, but also work on other Asian import vehicles. We have been in business for 7 years and pride ourselves on high quality auto repair that is fixed right the first time. Would like the automotive repair website to incorporate the colors black, red and white if possible and have our logo and some Navoro and Omvar vehicles included in the website.

Target Market(s)

Navoro & Omvar vehicle owners

Industry/Entity Type

Automotive Repair

Coding

Coded - Design and coding required

Number of Pages Required

5+ page

Colors
EB3D1F
EC4F4E
F09395
F8D3D4
FCEDEE

Requirements
Must have
• Home, Services, Contact Us, Schedule appointment, and a gallery tab that I can add shop pictures to when completed.
Nice to have
• Would like to see example pictures of job next to each service listed.
Should not have
• Service not related to auto repair. Ex. auto detailing, towing, car wash

```html
<!DOCTYPE html>
<html lang="en">
<head>
<meta charset="utf-8">
<title>Oil Change | Rexford Automotive</title>
<link href="https://fonts.googleapis.com/css2?family=Fira+Sans+Extra+Condensed:wght@400;500;600&family=Open+Sans:ital,wght@0,400;0,600;0,700;1,400;1,600&display=swap" rel="stylesheet">
<style>
:root{
  --red:#e8000b;
  --red-deep:#b8000a;
  --black:#0e0e0e;
  --charcoal:#2d2d2d;
  --panel:#f1f1f1;
  --white:#fff;
  --text:#555;
  --heading:#151515;
  --cond:"Fira Sans Extra Condensed",sans-serif;
  --body:"Open Sans",sans-serif;
}
*{box-sizing:border-box;margin:0;padding:0}
html,body{width:1200px;height:3529px;overflow:hidden}
body{position:relative;background:var(--white);font-family:var(--body);color:var(--text)}
.abs{position:absolute}
/* header */
.site-header{left:0;top:0;width:1200px;height:120px;background:var(--black)}
.header-rule{left:0;top:118px;width:380px;height:4px;background:var(--red)}
.brand{left:124px;top:14px;width:124px;height:96px;display:flex;align-items:center;justify-content:center;gap:8px;color:var(--white);font-family:var(--cond);font-weight:600;font-size:22px;letter-spacing:1px}
.brand .dot{width:14px;height:14px;background:var(--red);border-radius:50%}
.perk{top:22px;display:flex;align-items:center;gap:10px;color:#ddd;font-size:13px;font-style:italic;line-height:16px}
.perk .ic{width:34px;height:34px;border-radius:50%;background:#444;display:flex;align-items:center;justify-content:center}
.perk b{color:var(--red);font-weight:600}
.stars{color:var(--red);font-size:16px;letter-spacing:1px;font-style:normal}
.nav{top:96px;left:582px;display:flex;gap:30px;font-size:11.5px;font-weight:700;color:var(--white)}
.nav .on{color:var(--red)}
/* hero */
.hero{left:0;top:122px;width:1200px;height:314px;background:linear-gradient(90deg,#3a0c0c 0%,#7a1616 35%,#4a3a30 60%,#2a2a2a 100%)}
.hero-kicker{left:111px;top:228px;color:#eee;font-size:10px;font-weight:700;letter-spacing:.5px;display:flex;align-items:center;gap:10px}
.hero-kicker:before{content:"";width:40px;height:1px;background:#ddd}
.hero-title{left:111px;top:246px;color:var(--white);font-family:var(--cond);font-size:48px;font-weight:500;line-height:56px}
.hero-text{left:111px;top:308px;width:250px;color:#eee;font-size:11px;line-height:16px}
/* sidebar */
.sidebar{left:112px;top:530px;width:254px;height:858px;background:var(--charcoal)}
.sidebar h3{position:absolute;left:20px;top:34px;color:var(--white);font-family:var(--cond);font-style:italic;font-weight:500;font-size:18px}
.sidebar hr{position:absolute;left:20px;top:74px;width:210px;border:0;border-top:1px solid #555}
.svc-list{position:absolute;left:20px;top:98px;list-style:none;color:#e6e6e6;font-family:var(--cond);font-size:12px}
.svc-list li{display:flex;gap:8px;height:30px;line-height:15px}
.svc-list li.two{height:47px}
.svc-list li:before{content:"";flex:0 0 14px;height:8px;margin-top:2px;border-left:2px solid var(--red);border-bottom:2px solid var(--red);transform:rotate(-45deg) scale(.8)}
.help{left:112px;top:1388px;width:254px;height:201px;background:var(--red);color:var(--white);text-align:center}
.help h4{margin-top:28px;font-family:var(--cond);font-weight:500;font-size:19px;line-height:21px}
.help .call{width:40px;height:40px;border-radius:50%;background:var(--black);margin:14px auto 6px;display:flex;align-items:center;justify-content:center}
.help small{display:block;font-size:10px;font-weight:700}
.help strong{font-size:21px;font-weight:600}
/* main */
.kicker{color:var(--red);font-size:10px;font-weight:600;display:flex;align-items:center;gap:10px}
.kicker:before{content:"";width:40px;height:1px;background:var(--red)}
.h2{font-family:var(--cond);color:var(--heading);font-weight:500;font-size:36px;line-height:38px}
.p{font-size:11px;line-height:20px;color:var(--text)}
.price-card{left:834px;top:530px;width:255px;height:484px}
.price-card .photo{position:absolute;left:0;top:0;width:255px;height:210px;background:linear-gradient(160deg,#5a4a40,#2e2622)}
.price-card .body{position:absolute;left:0;top:210px;width:255px;height:274px;background:linear-gradient(#c8000a,var(--red-deep));clip-path:polygon(0 0,100% 0,100% 100%,30% 92%,0 100%)}
.badge{position:absolute;left:166px;top:16px;width:72px;height:72px;border-radius:50%;background:#f5b400;color:var(--heading);text-align:center;font-family:var(--cond);font-weight:600;font-size:32px;line-height:34px;padding-top:10px}
.badge small{display:block;font-size:8px;line-height:8px}
.price-card h4{position:absolute;left:25px;top:32px;color:var(--white);font-family:var(--cond);font-weight:500;font-size:20px}
.price-card .sub{position:absolute;left:25px;top:60px;color:#fff;font-size:10px}
.price-card .inc{position:absolute;left:25px;top:108px;color:#fff;font-size:10px;line-height:12.5px}
.price-card .inc b{display:block;font-family:var(--cond);font-size:13px;font-weight:600;margin-bottom:6px}
.price-card ul{padding-left:12px}
.btn{display:flex;align-items:center;justify-content:center;gap:8px;background:var(--black);color:var(--white);font-family:var(--cond);font-weight:600;font-size:12px;letter-spacing:.3px}
.benefit{top:1644px;width:153px;height:164px;color:var(--white);padding:20px 18px}
.benefit h5{font-family:var(--cond);font-weight:500;font-size:16px;margin:14px 0 4px}
.benefit p{font-size:9.5px;line-height:12px}
/* faq */
.faq{left:415px;top:1852px;width:674px;height:552px;background:var(--panel)}
.faq-item{position:absolute;left:48px;width:578px;height:42px;background:var(--white);display:flex;align-items:center;padding:0 14px;font-family:var(--cond);font-size:14px;color:var(--heading);justify-content:space-between}
.faq-item span b{color:var(--red);font-weight:500;margin-right:6px}
.faq-item.open{background:var(--red);color:var(--white)}
.faq-item.open span b{color:var(--white)}
/* cta */
.cta-bg{left:0;top:2507px;width:1200px;height:621px;background:linear-gradient(90deg,#555 0%,#2b2b2b 40%,#151515 100%);clip-path:polygon(0 10%,100% 0,100% 100%,0 100%)}
.cta-stripe{left:55px;top:2504px;width:1145px;height:30px}
.mechanic-photo{left:0;top:2540px;width:620px;height:588px;background:linear-gradient(180deg,#8a8d94 0%,#5f6a82 45%,#2c4584 100%)}
.field{position:absolute;left:619px;width:470px;background:var(--white);display:flex;justify-content:space-between;align-items:flex-start;padding:14px 14px;font-size:11px;font-style:italic;color:#999}
.field .ic{width:20px;height:20px;border:1.5px solid #555;border-radius:50%;flex:0 0 20px}
/* footer */
.footer{left:0;top:3128px;width:1200px;height:401px;background:var(--black)}
.f-head{color:var(--red);font-family:var(--cond);font-size:18px;font-weight:500}
.f-links{list-style:none;color:#ddd;font-size:11px;line-height:32px}
.f-contact{color:#ddd;font-size:11px;line-height:15px}
.f-contact .row{display:flex;align-items:center;gap:14px;height:46px}
.f-contact .ic{width:28px;height:28px;border-radius:50%;background:#3a3a3a;flex:0 0 28px}
.f-contact em{color:var(--red);font-style:normal}
.social{width:30px;height:30px;border-radius:50%;background:#3b3b3b;border:1px solid #666}
</style>
</head>
<body>

<header class="abs site-header"></header>
<div class="abs header-rule"></div>
<div class="abs brand"><span class="dot"></span>REXFORD</div>

<div class="abs perk" style="left:518px"><span class="ic"></span><div><span class="stars">★★★★★</span><br>5 Star Service</div></div>
<div class="abs perk" style="left:714px"><span class="ic"></span><div>Quality Service<br><b>Guarantee</b></div></div>
<div class="abs perk" style="left:920px"><span class="ic"><svg width="16" height="16" viewBox="0 0 24 24"><path fill="#fff" d="M6.6 10.8a15 15 0 006.6 6.6l2.2-2.2c.3-.3.7-.4 1-.2 1.1.4 2.3.6 3.6.6.6 0 1 .4 1 1V20c0 .6-.4 1-1 1A17 17 0 013 4c0-.6.4-1 1-1h3.5c.6 0 1 .4 1 1 0 1.3.2 2.5.6 3.6.1.3 0 .7-.2 1z"/></svg></span><div>Call Us For Booking<br><b>555.013.9110</b></div></div>

<nav class="abs nav"><span>HOME</span><span>ABOUT US</span><span class="on">SERVICES ⌄</span><span>GALLERY</span><span>TESTIMONIALS</span><span>CONTACT US</span></nav>

<section class="abs hero" role="img" aria-label="Motor oil pouring from a bottle into an engine"></section>
<div class="abs hero-kicker">PRESERVES ENGINE LIFE</div>
<h1 class="abs hero-title">Oil Change</h1>
<p class="abs hero-text">Quisque lorem neque, ultricies eget risus quis, fringilla interdum augue. Donec sollicitudin in ante sed consequat.</p>
<svg class="abs" style="left:0;top:434px" width="1200" height="42"><polygon points="329,4 1200,0 1200,20 372,40" fill="#e8000b"/></svg>

<aside class="abs sidebar">
  <svg style="position:absolute;right:0;top:0" width="70" height="76"><polygon points="0,0 70,76 70,0" fill="#fff"/></svg>
  <h3>Services We Provide</h3><hr>
  <ul class="svc-list">
    <li>Oil Changes</li><li>Computer Diagnostics</li><li>Electrical Specialists</li><li>Tires</li>
    <li>Tire Balance &amp; Rotations</li><li>Pre Purchase Inspections</li><li>Insurance Claims</li>
    <li>Emission Repair &amp; Catalytic Converters</li><li>Engine Repair</li><li>Heating &amp; AC Repair</li>
    <li>State Inspection</li><li>Suspension Service &amp; Repair</li><li>Leveling Kits &amp; Minor Lift Kit installation</li>
    <li>Brakes Service &amp; Repair</li><li>Exhaust, Muffler Service &amp; Repair</li>
    <li class="two">Automatic, Manual, Computerized<br>Transmission Service &amp; Repair</li>
    <li>Clutch Service &amp; Repair</li><li>CV Axle Service &amp; Repair</li>
    <li class="two">Fuel Injection System Service,<br>Cleaning &amp; Repair</li>
    <li>Timing Belts &amp; Water Pumps</li><li>Radiators &amp; Fans Service &amp; Repair</li>
    <li>Tune ups &amp; Factory Scheduled Maintenance</li><li>Hybrid Vehicle diagnostic &amp; repair</li><li>24-hr Night Drop</li>
  </ul>
</aside>
<div class="abs help">
  <h4>Dont see a service you<br>need? Contact us</h4>
  <div class="call"><svg width="18" height="18" viewBox="0 0 24 24"><path fill="#fff" d="M6.6 10.8a15 15 0 006.6 6.6l2.2-2.2c.3-.3.7-.4 1-.2 1.1.4 2.3.6 3.6.6.6 0 1 .4 1 1V20c0 .6-.4 1-1 1A17 17 0 013 4c0-.6.4-1 1-1h3.5c.6 0 1 .4 1 1 0 1.3.2 2.5.6 3.6.1.3 0 .7-.2 1z"/></svg></div>
  <small>Need Help?</small><strong>555.013.9110</strong>
</div>

<div class="abs kicker" style="left:416px;top:533px">SERVICES</div>
<h2 class="abs h2" style="left:416px;top:556px;width:380px">A Quick And Affordable Oil Change At Rexford Repair</h2>
<p class="abs p" style="left:416px;top:652px;width:370px">Lorem ipsum dolor sit amet, consectetur adipiscing elit. Ut non ipsum eleifend turpis vulputate pulvinar sit amet quis nulla. Vestibulum luctus nibh ligula, nec condimentum velit facilisis a. Nam cursus eu turpis a lacinia. Ut efficitur tortor hendrerit dui condimentum, quis volutpat nisl dapibus. Pellentesque vel magna feugiat, pretium nunc at, rhoncus ante. Ut sagittis lorem quis leo dapibus, et mollis enim finibus. Mauris scelerisque sodales nibh eget pretium.</p>
<div class="abs" style="left:416px;top:815px;width:369px;height:203px;background:linear-gradient(135deg,#8a8e92,#3a3d40);clip-path:polygon(8% 0,100% 0,100% 100%,0 100%,0 14%)" role="img" aria-label="Oil being poured into an engine filler"></div>

<div class="abs price-card">
  <div class="photo" role="img" aria-label="Mechanic pouring fresh oil from a jug"></div>
  <div class="badge">$45<small>Per Change</small></div>
  <div class="body">
    <h4>Oil And Filter Changes</h4>
    <div class="sub">Change your oil every 10,000 miles</div>
    <div class="inc"><b>This Service Includes:</b>
      <ul><li>Draining out old motor oil</li><li>Adding correct level of new oil</li><li>Replacing old oil filter</li><li>Checking the level of other fluids</li></ul>
    </div>
  </div>
</div>
<div class="abs btn" style="left:856px;top:944px;width:212px;height:42px">▣ SCHEDULE AN APPOINTMENT</div>

<div class="abs" style="left:416px;top:1056px;width:673px;height:247px;background:linear-gradient(120deg,#a9adb2,#50555a 60%,#7a7d80)" role="img" aria-label="Technician wiping an engine bay"></div>

<h2 class="abs h2" style="left:416px;top:1336px">Signs You Need An Oil Change</h2>
<p class="abs p" style="left:416px;top:1390px;width:673px">Lorem ipsum dolor sit amet, consectetur adipiscing elit. Ut non ipsum eleifend turpis vulputate pulvinar sit amet quis nulla. Vestibulum luctus nibh ligula, nec condimentum velit facilisis a. Nam cursus eu turpis a lacinia. Ut efficitur tortor hendrerit dui condimentum, quis volutpat nisl dapibus. Pellentesque vel magna feugiat, pretium nunc at, rhoncus ante. Ut sagittis lorem quis leo dapibus, et mollis enim finibus. Mauris scelerisque sodales nibh eget pretium. Aliquam molestie felis dolor, sed congue lacus ornare hendrerit. Sed sit amet sem ipsum. Nam purus ante, posuere at mauris ac, tempus condimentum velit. Nullam enim magna, feugiat a mattis sed, aliquam vel massa. Curabitur ac libero aliquet, dignissim purus in, maximus urna. In turpis turpis, condimentum id massa in, consequat pretium diam. Nunc facilisis quam.</p>
<p class="abs p" style="left:416px;top:1550px;width:673px">Pellentesque posuere consequat metus, non consectetur neque pretium et. Proin dapibus lorem a erat faucibus congue. Nullam in ipsum condimentum, pretium ipsum nec, suscipit mauris. Donec id laoreet ante. Sed malesuada in mauris ut sodales. Aenean neque est, placerat nec nisi eu, suscipit aliquet lorem. Class aptent taciti sociosqu.</p>

<h2 class="abs h2" style="left:416px;top:1638px">Key Benefits of<br>the Service</h2>
<svg class="abs" style="left:474px;top:1678px" width="114" height="8"><path d="M2 6 Q57 0 112 4" stroke="#e8000b" stroke-width="2" fill="none"/></svg>
<p class="abs p" style="left:416px;top:1728px;width:320px;line-height:18px">Lorem ipsum dolor sit amet, consectetur adipiscing elit. Ut non ipsum eleifend turpis vulputate pulvinar sit amet quis nulla. Vestibulum luctus nibh ligul.</p>
<div class="abs benefit" style="left:770px;background:var(--charcoal);clip-path:polygon(14% 0,100% 0,100% 100%,0 100%,0 12%)">
  <svg width="40" height="24" viewBox="0 0 40 24"><path fill="#fff" d="M6 6h6V3h10v3h6l4 4h4v10h-4l-4 3H10l-4-4H2V8h4z"/></svg>
  <h5>Longer Engine Life</h5><p>Lorem ipsum dolor sit amet, consectetur adipiscing elit.</p></div>
<div class="abs benefit" style="left:936px;background:var(--black);clip-path:polygon(14% 0,100% 0,100% 100%,0 100%,0 12%)">
  <svg width="26" height="30" viewBox="0 0 26 30"><circle cx="13" cy="19" r="10" fill="#fff"/><path d="M13 9 C8 2 4 4 5 8 C9 9 11 9 13 9 C15 4 20 2 21 6 C17 8 15 9 13 9" fill="#fff"/></svg>
  <h5>Earth Friendly</h5><p>Lorem ipsum dolor sit amet, consectetur adipiscing elit.</p></div>

<section class="abs faq">
  <div class="kicker" style="position:absolute;left:48px;top:52px">ASK ANYTHING</div>
  <h2 class="h2" style="position:absolute;left:48px;top:76px">Got A Question About<br>How We Operate?</h2>
  <div class="faq-item open" style="top:184px"><span><b>Q.</b>Sed non varius augue. Fusce a felis in dui faucibus porttitor?</span><span>⌃</span></div>
  <p class="p" style="position:absolute;left:62px;top:246px;width:400px">Lorem ipsum dolor sit amet, consectetur adipiscing elit. Ut non ipsum eleifend turpis vulputate pulvinar sit amet quis nulla.</p>
  <div class="faq-item" style="top:314px"><span><b>Q.</b>Sed non varius augue. Fusce a felis in dui faucibus porttitor?</span><span style="color:#e8000b">⌄</span></div>
  <div class="faq-item" style="top:362px"><span><b>Q.</b>Sed non varius augue. Fusce a felis in dui faucibus porttitor?</span><span style="color:#e8000b">⌄</span></div>
  <div class="faq-item" style="top:410px"><span><b>Q.</b>Sed non varius augue. Fusce a felis in dui faucibus porttitor?</span><span style="color:#e8000b">⌄</span></div>
  <div class="faq-item" style="top:458px"><span><b>Q.</b>Sed non varius augue. Fusce a felis in dui faucibus porttitor?</span><span style="color:#e8000b">⌄</span></div>
</section>

<section class="abs cta-bg" role="img" aria-label="Workshop with lifted vehicle in the background"></section>
<div class="abs mechanic-photo" role="img" aria-label="Photo of a smiling mechanic in blue overalls holding a wrench"></div>
<svg class="abs cta-stripe" width="1145" height="30"><polygon points="0,10 80,2 830,8 1145,24 1145,28 830,18 80,14" fill="#e8000b"/></svg>
<div class="abs kicker" style="left:932px;top:2590px">GET AN APPOINTMENT</div>
<h2 class="abs h2" style="left:700px;top:2614px;width:389px;color:#fff;text-align:right">Your Source For Reliable<br>And Efficient Repairs</h2>
<svg class="abs" style="left:660px;top:2618px" width="440" height="130"><path d="M160 82 Q300 68 410 76" stroke="#e8000b" stroke-width="2" fill="none"/><path d="M66 14 Q4 40 14 104" stroke="#fff" stroke-width="1.5" fill="none"/><path d="M9 98 L14 106 L19 98" stroke="#fff" stroke-width="1.5" fill="none"/></svg>
<p class="abs p" style="left:700px;top:2726px;width:389px;color:#eee;text-align:right;line-height:17px">Contact us for a free estimate! Please include year, make, and model and the service or repair you would like  an estimate on.</p>
<div class="field" style="top:2784px;height:42px;color:#222">Jordan Lee |<span class="ic"></span></div>
<div class="field" style="top:2831px;height:42px">+ 00 123 456 7890<span class="ic"></span></div>
<div class="field" style="top:2877px;height:42px">info@jordanlee.com<span class="ic"></span></div>
<div class="field" style="top:2924px;height:86px">Message<span class="ic"></span></div>
<div class="abs btn" style="left:860px;top:3014px;width:229px;height:43px;background:var(--red);clip-path:polygon(8% 0,100% 0,100% 100%,0 100%,0 30%)">▣ SCHEDULE AN APPOINTMENT</div>

<footer class="abs footer"></footer>
<div class="abs brand" style="left:112px;top:3208px;width:188px;height:120px;font-size:28px"><span class="dot"></span>REXFORD</div>
<div class="abs" style="left:112px;top:3348px;width:90px;height:36px;background:#fff"></div>
<div class="abs" style="left:210px;top:3348px;width:76px;height:36px;background:#fff"></div>
<div class="abs" style="left:112px;top:3390px;width:50px;height:36px;background:#fff"></div>
<div class="abs" style="left:168px;top:3390px;width:90px;height:36px;background:#fff"></div>

<div class="abs f-head" style="left:367px;top:3194px">Quick Links.</div>
<ul class="abs f-links" style="left:367px;top:3226px"><li>Home</li><li>About Us</li><li>Services</li><li>Gallery</li><li>Testimonials</li><li>Contact Us</li></ul>
<div class="abs f-head" style="left:515px;top:3194px">Contact Us</div>
<div class="abs f-contact" style="left:507px;top:3228px">
  <div class="row"><span class="ic"></span><span>418 Harbor Loop #5<br>Fairmont, TX 75000</span></div>
  <div class="row"><span class="ic"></span><span><em>OFFICE:</em> 555.013.9110<br><em>Phone:</em> 555.014.7493</span></div>
  <div class="row"><span class="ic"></span><span>RexfordAutoLLC@mailbox.com</span></div>
  <div class="row"><span class="ic"></span><span><em>Hours of Operation:</em> M-F 8:30-6pm</span></div>
</div>
<div class="abs" style="left:793px;top:3191px;width:296px;height:207px;background:linear-gradient(135deg,#e9eef0,#d6e2ea);clip-path:polygon(8% 0,100% 0,100% 100%,0 100%,0 12%)" role="img" aria-label="Map showing the shop location"></div>

<div class="abs social" style="left:150px;top:3480px"></div>
<div class="abs social" style="left:184px;top:3480px"></div>
<div class="abs social" style="left:218px;top:3480px"></div>
<svg class="abs" style="left:0;top:3488px" width="1200" height="41"><polygon points="352,0 1200,0 1200,41 322,41" fill="#e8000b"/><line x1="330" y1="0" x2="300" y2="41" stroke="#e8000b" stroke-width="4"/></svg>
<div class="abs" style="left:764px;top:3501px;color:#fff;font-size:11px;font-weight:600">Copyright © 2024 Rexford Automotive LLC. All Rights Reserved.</div>

</body>
</html>
```